SK regenerative food process graphic design for posters

We are a Hawaii snorkel tour company who makes all of our cruises vegan food from scratch and have a family farm we use for composting & growing food products. We want a design showing our food recycling process. From the soil to the tree's fruit to cooking, to eating, to zero-waste trash can, to recycle, to compost pile. Representing the complete circle in the process. We want you to use a breadfruit or ulu tree for our tree. We want to express our companies commitment to being good stewards to Hawaii and our planet's environmental health.

Target Market(s)

tourists, families traveling

Industry/Entity Type

Eco-tourism

Font styles to use
Sans Serif

Colors
59FF00
82FF00
B8FF75
E3FFCB
F4FFEA
FFC000
F8CF3A
FAE287
FDF2CF
FEFAEE

Requirements
Must have
• Small Silver Kettle logo on artwork showing ownership, Hand drawn artwork, with written explanation at each step of the process
Nice to have
• easy to understand artwork showing the process from farm to table and back again
Should not have
• stock images, graphics, photos

```html
<!DOCTYPE html>
<html lang="en">
<head>
<meta charset="utf-8">
<title>Silver Kettle – Food Recycling Process</title>
<link rel="stylesheet" href="https://fonts.googleapis.com/css2?family=Encode+Sans+Condensed:wght@700&family=Montserrat:wght@800&family=PT+Sans&family=Playfair+Display:ital@1&display=swap">
<style>
  :root {
    --backdrop: #2b2b2b;
    --paper: #eaf2d7;
    --ink: #1c1c1c;
    --band: #7dc242;
    --band-shadow: #9aa38c;
    --dirt: #ef5a5f;
    --ulu: #fbb21e;
    --mixing: #b3d334;
    --eating: #2e8b3f;
    --trash: #43a3dc;
    --recycle: #33479a;
    --compost: #a2278f;
    --white: #ffffff;
  }
  * { margin: 0; padding: 0; box-sizing: border-box; }
  html, body { width: 1200px; height: 1200px; overflow: hidden; }
  body { background: var(--backdrop); position: relative; font-family: "PT Sans", sans-serif; }
  .poster {
    position: absolute; left: 205px; top: 47px; width: 788px; height: 1105px;
    background: var(--paper);
  }
  .cycle { position: absolute; left: 0; top: 0; width: 1200px; height: 1200px; }
  .brand {
    position: absolute; left: 0; width: 1200px; top: 92px; text-align: center;
    font-family: "PT Sans", sans-serif; font-size: 44px; color: var(--ink); letter-spacing: 1px;
  }
  .title-band {
    position: absolute; left: 243px; top: 230px; width: 712px; height: 68px;
    background: var(--band); box-shadow: 3px 3px 0 var(--band-shadow);
    display: flex; align-items: center; justify-content: center; gap: 18px;
    font-family: "Montserrat", sans-serif; font-weight: 800; font-size: 47px; color: var(--ink);
  }
  .title-band .dot { width: 12px; height: 12px; border-radius: 50%; background: var(--white); }
  .step { position: absolute; color: var(--white); text-align: center; transform: translateX(-50%); }
  .step h2 {
    font-family: "Encode Sans Condensed", sans-serif; font-weight: 700;
    font-size: 16px; line-height: 18.6px;
  }
  .step .rule { height: 2px; background: var(--ink); margin: 5px auto 4px; }
  .step p { font-size: 9.6px; line-height: 10.3px; }
</style>
</head>
<body>
<div class="poster"></div>

<svg class="cycle" viewBox="0 0 1200 1200" aria-hidden="false">
  <g stroke="var(--ink)" stroke-width="2">
    <ellipse cx="595" cy="422" rx="100" ry="105" fill="var(--dirt)"/>
    <ellipse cx="801" cy="546" rx="99" ry="130" fill="var(--ulu)"/>
    <ellipse cx="860" cy="807" rx="105" ry="118" fill="var(--mixing)"/>
    <ellipse cx="702" cy="1006" rx="108" ry="118" fill="var(--eating)"/>
    <ellipse cx="472" cy="1006" rx="105" ry="93" fill="var(--trash)"/>
    <ellipse cx="329" cy="789" rx="102" ry="118" fill="var(--recycle)"/>
    <ellipse cx="385" cy="515" rx="105" ry="124" fill="var(--compost)"/>
  </g>
  <g fill="none" stroke="var(--white)" stroke-width="2" stroke-linecap="round">
    <path d="M520 375 Q540 340 570 335"/>
    <path d="M740 470 Q760 430 800 430"/>
    <path d="M800 760 Q815 720 850 712"/>
    <path d="M660 920 Q690 900 730 900"/>
    <path d="M410 950 Q430 920 460 915"/>
    <path d="M245 800 Q245 760 262 735"/>
    <path d="M320 460 Q335 420 370 410"/>
  </g>
  <rect x="435" y="559" width="298" height="338" rx="140" fill="#8cc63f" opacity="0.85" role="img" aria-label="Hand-drawn breadfruit (ulu) tree with leafy green crown, fruit and spreading roots"/>

  <g stroke="var(--ink)" stroke-width="2.5" fill="var(--white)">
    <circle cx="689" cy="428" r="46"/>
    <circle cx="894" cy="649" r="46"/>
    <circle cx="845" cy="925" r="46"/>
    <circle cx="599" cy="1018" r="46"/>
    <circle cx="360" cy="956" r="46"/>
    <circle cx="295" cy="671" r="46"/>
    <circle cx="460" cy="441" r="46"/>
  </g>
  <circle cx="689" cy="428" r="30" fill="#b07a3a" role="img" aria-label="Sack of rich soil with a red trowel"/>
  <circle cx="894" cy="649" r="30" fill="#e8e2c0" role="img" aria-label="Sliced breadfruit with leaves"/>
  <circle cx="845" cy="925" r="30" fill="#f08a4b" role="img" aria-label="Mixing bowl with whisk"/>
  <circle cx="599" cy="1018" r="30" fill="#f2b36b" role="img" aria-label="Two guests enjoying a meal"/>
  <circle cx="360" cy="956" r="30" fill="#d9506f" role="img" aria-label="Person emptying scraps into a bin"/>
  <circle cx="295" cy="671" r="30" fill="#6d7a80" role="img" aria-label="Recycling bin with food scraps"/>
  <circle cx="460" cy="441" r="30" fill="#f4cf5a" role="img" aria-label="Compost crate with a shovel"/>
</svg>

<div class="brand">Silver Kettle</div>

<div class="title-band"><span class="dot"></span>Food Recycling Process<span class="dot"></span></div>

<section class="step" style="left:584px; top:352px; width:120px;">
  <h2>1. Dirt step</h2>
  <div class="rule" style="width:117px"></div>
  <p>Healthy soil, rich in<br>nutrients and organic<br>matter, starts with how<br>we treat our 'aina. Our<br>family farm follows<br>organic, bio-dynamic,<br>and Korean Natural<br>Farming practices,<br>preparing the soil<br>for planting</p>
</section>

<section class="step" style="left:803px; top:456px; width:160px;">
  <h2>2. 'Ulu/<br>breadfruit<br>step</h2>
  <div class="rule" style="width:157px"></div>
  <p>The organic produce we serve<br>is nutrient-dense and flavorful<br>and features some traditional<br>Hawaiian "canoe plants" -<br>plants the first Hawaiians<br>brought to Hawai'i from<br>Polynesia for food -<br>like 'ulu (breadfruit),<br>'uala (purple sweet<br>potato), and<br>mai'a (banana)</p>
</section>

<section class="step" style="left:863px; top:739px; width:150px;">
  <h2>3. Mixing bowl<br>step</h2>
  <div class="rule" style="width:114px"></div>
  <p>All food is prepared daily from<br>scratch in our 100% plant-based<br>kitchen with taste and nutritional<br>content in mind, as well as being<br>cruelty-free towards animals and<br>the environment</p>
</section>

<section class="step" style="left:718px; top:918px; width:120px;">
  <h2>4. People eating<br>step</h2>
  <div class="rule" style="width:115px"></div>
  <p>Make memories of<br>snorkeling in<br>beautiful Kealakekua<br>and enjoy an<br>exclusive foodie<br>experience<br>of healthful,<br>plant-based cuisine<br>as you've never<br>experienced<br>before</p>
</section>

<section class="step" style="left:475px; top:940px; width:110px;">
  <h2>5. Trash can<br>step</h2>
  <div class="rule" style="width:92px"></div>
  <p>Silver Kettle<br>snorkel tours<br>are zero-waste<br>and do not<br>produce trash<br>for the landfill</p>
</section>

<section class="step" style="left:331px; top:739px; width:130px;">
  <h2>6. Recycle step</h2>
  <div class="rule" style="width:129px"></div>
  <p>We recycle all<br>cardboard, cans, and<br>bottles. Any leftover<br>or waste products<br>from our kitchen &amp;<br>meals are collected<br>for composting on<br>our farm</p>
</section>

<section class="step" style="left:374px; top:463px; width:132px;">
  <h2>7. Compost<br>step</h2>
  <div class="rule" style="width:131px"></div>
  <p>The organic materials we<br>collect break down<br>over time into nutrient-rich<br>compost which we use<br>on our farm<br>to grow produce<br>served on<br>our tours</p>
</section>
</body>
</html>
```